VOMRA Pty Ltd Business Card

Looking for a simple yet eye-catching double-sided business card design using my company logo on one side and contact details on the other.

Target Market(s)

Government

Industry/Entity Type

Communication Systems Engineering

Contact Information for Business Card

VOMRA Pty Ltd

Requirements
Nice to have
• Would be great to have a QR code so details can be scanned into contacts

```html
<!DOCTYPE html>
<html lang="en">
<head>
<meta charset="utf-8">
<title>VOMRA Pty Ltd Business Card</title>
<link rel="stylesheet" href="https://fonts.googleapis.com/css2?family=Montserrat:wght@400;500;600;700&display=swap">
<style>
  :root {
    --page-light: #e9eaeb;
    --page-dark: #9a9c9e;
    --card-light: #6f787e;
    --card-mid: #4a545b;
    --card-dark: #313b43;
    --ink-white: #f2f2f2;
    --ink-soft: #e4e6e7;
    --mark-muted: #8c959b;
  }
  * { box-sizing: border-box; margin: 0; padding: 0; }
  html, body { width: 1200px; height: 1200px; overflow: hidden; }
  body {
    background: linear-gradient(120deg, var(--page-light) 0%, #c9cacb 55%, var(--page-dark) 100%);
    font-family: "Montserrat", sans-serif;
    position: relative;
  }
  .card {
    position: absolute;
    left: 220px;
    width: 760px;
    height: 434px;
    border-radius: 26px;
    background: linear-gradient(110deg, var(--card-light) 0%, var(--card-mid) 40%, var(--card-dark) 75%);
    box-shadow: 0 14px 30px rgba(0,0,0,0.28);
    overflow: hidden;
  }
  .card--front { top: 140px; }
  .card--back { top: 626px; }

  .brand {
    position: absolute;
    display: flex;
    align-items: center;
    gap: 22px;
  }
  .brand__dot {
    width: 46px; height: 46px;
    border-radius: 50%;
    border: 3px solid currentColor;
  }
  .brand__name {
    font-weight: 600;
    letter-spacing: 2px;
    line-height: 1;
  }
  .card--front .brand {
    left: 50%; top: 50%;
    transform: translate(-50%, -50%);
    color: var(--mark-muted);
  }
  .card--front .brand__name { font-size: 92px; }
  .card--front .brand__dot { width: 70px; height: 70px; }

  .card--back .brand {
    left: 50%; top: 40px;
    transform: translateX(-50%);
    color: var(--ink-white);
  }
  .card--back .brand__name { font-size: 70px; }
  .card--back .brand__dot { width: 54px; height: 54px; border-color: #9aa3a8; }

  .person {
    position: absolute;
    left: 80px;
    top: 262px;
    color: var(--ink-white);
  }
  .person__name { font-size: 30px; font-weight: 700; }
  .person__role { font-size: 19px; font-weight: 400; margin-top: 6px; padding-left: 52px; color: var(--ink-soft); }

  .contact {
    position: absolute;
    left: 395px;
    top: 196px;
    color: var(--ink-soft);
    font-size: 19px;
    list-style: none;
  }
  .contact__item { display: flex; align-items: center; gap: 12px; height: 30px; }
  .contact__icon { width: 16px; height: 16px; fill: var(--ink-soft); flex: none; }
  .contact__address { margin-top: 10px; line-height: 28px; font-size: 19px; }
</style>
</head>
<body>
  <section class="card card--front" aria-label="Card front">
    <div class="brand">
      <span class="brand__dot"></span>
      <span class="brand__name">VOMRA</span>
    </div>
  </section>

  <section class="card card--back" aria-label="Card back">
    <div class="brand">
      <span class="brand__dot"></span>
      <span class="brand__name">VOMRA</span>
    </div>

    <div class="person">
      <p class="person__name">Dorian Vale</p>
      <p class="person__role">Founder &amp; Director</p>
    </div>

    <ul class="contact">
      <li class="contact__item">
        <svg class="contact__icon" viewBox="0 0 16 16" aria-hidden="true"><path d="M3.2 1.5l2.3 2.6-1.2 1.6c.9 2 2.4 3.5 4.4 4.4l1.6-1.2 2.6 2.3-1.3 2.1C6.8 13.1 2.9 9.2 1.1 2.8z"/></svg>
        (405)-555-0147
      </li>
      <li class="contact__item">
        <svg class="contact__icon" viewBox="0 0 16 16" aria-hidden="true"><path d="M1 3h14v10H1z M1 3l7 6 7-6" fill="none" stroke="#e4e6e7" stroke-width="1.5"/></svg>
        admin@vomra.com.au
      </li>
      <li class="contact__item">
        <svg class="contact__icon" viewBox="0 0 16 16" aria-hidden="true"><g fill="none" stroke="#e4e6e7" stroke-width="1.4"><circle cx="8" cy="8" r="6.5"/><ellipse cx="8" cy="8" rx="2.8" ry="6.5"/><path d="M1.5 8h13"/></g></svg>
        www.vomra.com.au
      </li>
      <li class="contact__address">42-44 Harlow Street Eastmere<br>NSW 2010 Australia</li>
    </ul>
  </section>
</body>
</html>
```